Business card design for holistic health care clinic

We need a double-sided business card design for our holistic health care clinic that integrates our logo design and also its color scheme. My business is called Valmira. It is an integrative medicine clinic. You have already done the logo for me. Please ensure an elegant and upscale design that is not cluttered, but still has all the necessary information (please see below for details).

Target Market(s)

Wellness, fitness, rehabilitation for educated, well-traveled open-minded clients who are focused on natural, organic, balanced and preventive healthcare and lifestyle.

Industry/Entity Type

Medical

Contact Information for Business Card

Modern, clean.

Number of Pages Required

1 page

Font styles to use
Serif
Sans Serif

Colors

Designer to choose colors to be used in the design.

Requirements
Must have
• Logo on one side, all other information on the other side.
• Other information should include:
• Tobias Wrenfeld - DOE, CPT, LMT
• 4100 East Marrow Drive
• Austin, TX 78119
• 512 555 0148
• 818 555 0192
• info@ValmiraHealth.example
• t.wrenfeld@ValmiraHealth.example
Nice to have
• Darker background on front - but not totally black - shaded/dark gray.

```html
<!DOCTYPE html>
<html lang="en">
<head>
<meta charset="utf-8">
<title>Valmira Business Card</title>
<link rel="stylesheet" href="https://fonts.googleapis.com/css2?family=Nunito+Sans:wght@400;600;700;800&display=swap">
<style>
  :root {
    --page-bg: #e9e6e1;
    --card-dark: #2a2d32;
    --card-mid: #383b40;
    --brand-blue: #1f93d8;
    --band-blue: #1a8fd1;
    --text-light: #f2f3f5;
    --card-radius: 26px;
  }
  * { box-sizing: border-box; margin: 0; padding: 0; }
  html, body {
    width: 1200px;
    height: 969px;
    overflow: hidden;
    background: var(--page-bg);
    font-family: "Nunito Sans", sans-serif;
  }
  .canvas {
    position: relative;
    width: 1200px;
    height: 969px;
  }
  .business-card {
    position: absolute;
    left: 100px;
    top: 200px;
    width: 1000px;
    height: 568px;
    border-radius: var(--card-radius);
    overflow: hidden;
    background: linear-gradient(135deg, var(--card-mid) 0%, var(--card-dark) 55%, #25282c 100%);
    box-shadow: 0 18px 40px rgba(0,0,0,0.22);
  }
  .brand {
    position: absolute;
    left: 57px;
    top: 108px;
  }
  .brand-name {
    display: flex;
    align-items: center;
    gap: 16px;
    font-weight: 800;
    font-size: 74px;
    line-height: 1;
    letter-spacing: 1px;
    color: var(--brand-blue);
    text-transform: uppercase;
  }
  .brand-dot {
    width: 22px;
    height: 22px;
    border-radius: 50%;
    background: var(--brand-blue);
  }
  .brand-tagline {
    margin-top: 10px;
    font-weight: 700;
    font-size: 23px;
    color: var(--brand-blue);
    padding-left: 6px;
  }
  .address {
    position: absolute;
    left: 62px;
    top: 266px;
    font-size: 23px;
    line-height: 30px;
    color: var(--text-light);
  }
  .contact-list {
    position: absolute;
    left: 62px;
    top: 340px;
    list-style: none;
    font-size: 23px;
    line-height: 33px;
    color: var(--text-light);
  }
  .contact-list li {
    display: flex;
    align-items: center;
    gap: 14px;
  }
  .contact-list svg {
    width: 20px;
    height: 20px;
    fill: var(--brand-blue);
    flex: none;
  }
  .person {
    position: absolute;
    right: 70px;
    top: 328px;
    text-align: right;
    color: var(--brand-blue);
  }
  .person-name {
    font-weight: 800;
    font-size: 33px;
    line-height: 1.1;
    text-transform: uppercase;
  }
  .person-credentials {
    font-weight: 700;
    font-size: 19px;
    margin-top: 4px;
  }
  .slogan-band {
    position: absolute;
    left: 0;
    right: 0;
    bottom: 0;
    height: 52px;
    background: var(--band-blue);
    display: flex;
    align-items: center;
    padding-left: 190px;
    font-weight: 700;
    font-size: 22px;
    color: #ffffff;
  }
</style>
</head>
<body>
<main class="canvas">
  <section class="business-card">
    <div class="brand">
      <div class="brand-name"><span class="brand-dot"></span>Valmira</div>
      <p class="brand-tagline">Integrative Holistic Medicine</p>
    </div>

    <address class="address" style="font-style: normal;">
      4100 East Marrow Drive<br>
      Austin, TX 78119
    </address>

    <ul class="contact-list">
      <li>
        <svg viewBox="0 0 24 24" aria-hidden="true"><path d="M6.6 10.8a15.1 15.1 0 0 0 6.6 6.6l2.2-2.2a1 1 0 0 1 1-.25 11.4 11.4 0 0 0 3.6.57 1 1 0 0 1 1 1V20a1 1 0 0 1-1 1A17 17 0 0 1 3 4a1 1 0 0 1 1-1h3.5a1 1 0 0 1 1 1c0 1.25.2 2.45.57 3.57a1 1 0 0 1-.25 1z"/></svg>
        512 555 0148
      </li>
      <li>
        <svg viewBox="0 0 24 24" aria-hidden="true"><path d="M7 1h10a2 2 0 0 1 2 2v18a2 2 0 0 1-2 2H7a2 2 0 0 1-2-2V3a2 2 0 0 1 2-2zm0 4v13h10V5zm5 14.5a1.2 1.2 0 1 0 0 2.4 1.2 1.2 0 0 0 0-2.4z"/></svg>
        818 555 0192
      </li>
      <li>
        <svg viewBox="0 0 24 24" aria-hidden="true"><path d="M2 5h20v14H2zm2 2v.5l8 5 8-5V7l-8 5z"/></svg>
        t.wrenfeld@ValmiraHealth.example
      </li>
      <li>
        <svg viewBox="0 0 24 24" aria-hidden="true"><path d="M12 2a10 10 0 1 0 0 20 10 10 0 0 0 0-20zm-1 17.9A8 8 0 0 1 4.2 10.4L9 15v1a2 2 0 0 0 2 2zm6.9-2.5A2 2 0 0 0 16 16h-1v-3a1 1 0 0 0-1-1H8v-2h2a1 1 0 0 0 1-1V7h2a2 2 0 0 0 2-2v-.4a8 8 0 0 1 2.9 12.8z"/></svg>
        www.ValmiraHealth.example
      </li>
    </ul>

    <div class="person">
      <p class="person-name">Tobias Wrenfeld</p>
      <p class="person-credentials">DOE, CPT, LMT</p>
    </div>

    <footer class="slogan-band">At Valmira, it’s all about you – your health, your objectives</footer>
  </section>
</main>
</body>
</html>
```